Stationery Design Project

I need a stationary design for our company. we are based in Houston, TX and we are called Mira Vell Lending. And we are wanting to brand our MoneyMendPlus program, which includes our tax preparation and restoration, credit repair service. Although our business offers other programs, we are interested in mainly focusing on The MoneyMendPlus program. We are looking for way to brand our ourselves and I believe that a great stationery design will help in achieving this goal. Our logo design is blue and light blue. the slogan is orange.

Industry/Entity Type

Business

Requirements
Must have
• Address: 30871 Calloway Ln. B-22
Houston, TX 75419
Tel. 555-318-6207
Fax 555-294-7153
www.miravelllending.example
info@miravelllending.example
Our Slogan: Confidence, Renewed!

```html
<!DOCTYPE html>
<html lang="en">
<head>
<meta charset="utf-8">
<title>MoneyMendPlus Business Card</title>
<link rel="stylesheet" href="https://fonts.googleapis.com/css2?family=Crimson+Text:wght@400;600;700&display=swap">
<style>
  :root {
    --bg: #e9e7e3;
    --card: #ffffff;
    --navy: #123e68;
    --blue-deep: #184f86;
    --blue-bright: #1a8fcc;
    --brand-blue: #1d6aa8;
    --light-blue: #cfe3f3;
    --frame-blue: #9bbbd6;
    --orange: #f29a27;
    --white: #ffffff;
    --ink: #30343a;
  }
  * { box-sizing: border-box; margin: 0; padding: 0; }
  html, body {
    width: 1200px; height: 714px; overflow: hidden;
    background: var(--bg);
    font-family: "Crimson Text", Georgia, serif;
  }
  .stage {
    width: 1200px; height: 714px;
    display: flex; align-items: center; justify-content: center; gap: 48px;
  }
  .card {
    position: relative;
    width: 540px; height: 312px;
    background: var(--card);
    border-radius: 26px;
    overflow: hidden;
    box-shadow: 0 6px 18px rgba(0,0,0,0.14);
  }

  /* Front */
  .brand {
    position: absolute; left: 0; top: 0; width: 272px; height: 100%;
    display: flex; flex-direction: column; align-items: center; justify-content: center;
    padding-top: 28px;
  }
  .brand-mark {
    width: 32px; height: 32px; border-radius: 50%;
    background: var(--brand-blue); margin-bottom: 12px;
  }
  .brand-name {
    color: var(--brand-blue);
    font-size: 33px; font-weight: 400; line-height: 1;
    white-space: nowrap;
  }
  .slogan {
    color: var(--orange);
    font-size: 20px; margin-top: 10px;
    white-space: nowrap;
  }
  .url-band {
    position: absolute; left: 272px; top: 0;
    width: 28px; height: 262px;
    background: var(--orange);
    display: flex; align-items: center; justify-content: center;
  }
  .url-band span {
    transform: rotate(-90deg);
    white-space: nowrap;
    color: var(--navy);
    font-size: 13px; letter-spacing: 0.3px;
  }
  .contact-panel {
    position: absolute; left: 300px; top: 0; right: 0; height: 262px;
    background: linear-gradient(180deg, var(--blue-deep) 0%, var(--blue-bright) 100%);
    color: var(--white);
    padding: 78px 14px 0 20px;
    font-size: 15px; line-height: 1.2;
  }
  .address { margin-bottom: 14px; }
  .contact-line {
    display: flex; align-items: center; gap: 8px; margin-bottom: 4px;
    white-space: nowrap;
  }
  .contact-line svg { width: 12px; height: 12px; flex: none; }

  /* Back */
  .emblem {
    position: absolute; left: 50%; top: 42px; transform: translateX(-50%);
    width: 216px; height: 216px;
    background: var(--light-blue);
    padding: 6px;
    border: 1px solid var(--frame-blue);
  }
  .emblem-inner {
    width: 100%; height: 100%;
    background: var(--navy);
    display: flex; align-items: flex-end; justify-content: center;
    padding-bottom: 30px;
  }
  .emblem-name {
    color: var(--white);
    font-size: 20px; font-weight: 400;
    white-space: nowrap;
  }
  .web-line {
    position: absolute; left: 0; right: 0; bottom: 20px;
    text-align: center;
    color: var(--ink);
    font-size: 13px; letter-spacing: 4px;
    white-space: nowrap;
  }
  .web-line strong { color: var(--navy); font-weight: 700; font-size: 16px; }
</style>
</head>
<body>
<main class="stage">
  <section class="card card-front">
    <div class="brand">
      <div class="brand-mark"></div>
      <div class="brand-name">MoneyMendPlus</div>
      <div class="slogan">Confidence, Renewed!</div>
    </div>
    <div class="url-band"><span>www.miravelllending.example</span></div>
    <div class="contact-panel">
      <p class="address">30871 Calloway Ln. B-22<br>Houston, TX 75419</p>
      <p class="contact-line">
        <svg viewBox="0 0 16 16" aria-hidden="true"><path fill="#fff" d="M3.5 1.5l2.5 0 1 3.5-1.6 1.2a9 9 0 0 0 4.4 4.4L11 9l3.5 1v2.5c0 1-1 2-2 2A11 11 0 0 1 1.5 3.5c0-1 1-2 2-2z"/></svg>
        555-318-6207
      </p>
      <p class="contact-line">
        <svg viewBox="0 0 16 16" aria-hidden="true"><rect x="4" y="1.5" width="8" height="4" fill="#fff"/><rect x="1" y="6" width="14" height="6" rx="1.5" fill="#fff"/><rect x="4" y="10" width="8" height="4.5" fill="#fff" stroke="#1a6fad" stroke-width="1"/></svg>
        555-294-7153
      </p>
      <p class="contact-line">
        <svg viewBox="0 0 16 16" aria-hidden="true"><rect x="1" y="3" width="14" height="10" rx="1.5" fill="#fff"/><path d="M1.5 4l6.5 5 6.5-5" fill="none" stroke="#1a7fbf" stroke-width="1.3"/></svg>
        info@miravelllending.example
      </p>
    </div>
  </section>

  <section class="card card-back">
    <div class="emblem">
      <div class="emblem-inner">
        <span class="emblem-name">Mira Vell Lending</span>
      </div>
    </div>
    <p class="web-line">www.<strong>miravelllending</strong>.example</p>
  </section>
</main>
</body>
</html>
```